Call Center In Need of Website Design

We are a call center that provides inbound and outbound calling & marketing services for eCommerce store. We would like to see a fun, creative, playful design that is simple.

Here are some sample design sites we like;
- https://www.velmoreline.com/
- https://pindrask.io/
- https://www.glimbertic.com/live-chat-software/
- https://www.zavrolin.com/

Here are some competitor sites;
- https://www.ostrevaglinks.com/
- https://www.helpkestrel.com/

I have attached website content for your use.

Target Market(s)

eCommerce

Coding

Coded - Design and coding required

Number of Pages Required

5+ page

Font styles to use
Sans Serif

Colors

Designer to choose colors to be used in the design.

Requirements
Must have
• Must have designs for the following 5 separate pages;
• 1. Home (landing)
• - This will be were the design style really needs to show.
• - Just needs to touch on key services
• - CTA
• 2. About Us
• - Basic page for about me paragraph
• 3. Services
• - List of services with icons
• - Click on service type to expand details or hover over service icon to view popup bubble with details about that service
• 4. Pricing
• - Option to bundle 1(one) digital service plan and 1(one) call center service plan
• - Bundling adds 10% monthly discount to over all price
• - Customer does NOT have to bundle
• - FAQ
• 5. Contact Us
• - Include a capture form (name, company name, email, phone, message)
• - Contact info
• - Business hours
• When customer purchases their desired plan, then they are taken to a page where they must schedule a call with an account rep.
Nice to have
• home page animations
Should not have
• All information on Home/Landing page.

```html
<!DOCTYPE html>
<html lang="en">
<head>
<meta charset="utf-8">
<title>Orbitra — Pricing</title>
<link href="https://fonts.googleapis.com/css2?family=Montserrat:wght@400;600;700;800;900&family=Open+Sans:wght@400;600;700&display=swap" rel="stylesheet">
<style>
:root{
  --space:#3b3780;
  --teal:#5ec9ad;
  --teal-dark:#3fae93;
  --teal-soft:#dff4ee;
  --teal-ink:#1f6f5e;
  --cloud:#bfeadf;
  --ink:#2a2a3a;
  --muted:#6b6f7d;
  --line:#e3e6ea;
  --white:#ffffff;
}
*{box-sizing:border-box;margin:0;padding:0}
html,body{width:1200px;height:2604px;overflow:hidden}
body{font-family:"Open Sans",sans-serif;color:var(--ink);background:var(--white);position:relative}
section,header,footer{position:absolute;left:0;width:1200px}

/* Hero */
.hero{top:0;height:420px;background:var(--space);overflow:hidden}
.nav{position:absolute;z-index:3;top:36px;left:90px;right:90px;display:flex;align-items:center;justify-content:space-between}
.brand{display:flex;align-items:center;gap:12px;color:var(--white);font-family:"Montserrat",sans-serif;font-weight:700;font-size:24px;letter-spacing:6px}
.brand-dot{width:22px;height:22px;background:var(--teal);border-radius:50%}
.menu{display:flex;gap:38px;list-style:none;font-family:"Montserrat",sans-serif;font-size:11px;font-weight:600;letter-spacing:1px;color:#cfcdea;text-transform:uppercase}
.menu .active{color:var(--white);border-bottom:2px solid var(--teal);padding-bottom:4px}
.hero-title{position:absolute;z-index:2;left:160px;top:158px;font-family:"Montserrat",sans-serif;font-weight:800;font-size:48px;line-height:56px;color:var(--white)}
.hero-sub{position:absolute;z-index:2;left:162px;top:282px;font-family:"Montserrat",sans-serif;font-size:16px;letter-spacing:3px;color:#d9d6f3}
.hero-rocket{position:absolute;left:62px;top:110px;width:26px;height:120px;border-radius:13px;background:linear-gradient(180deg,#7fe0c6,#3b3780)}
.hero-astronaut{position:absolute;z-index:1;left:780px;top:80px;width:360px;height:300px;border-radius:40%;background:radial-gradient(circle at 55% 45%,#e9ebf5 0,#b9bdd8 40%,rgba(59,55,128,0) 70%)}
.hero-clouds{position:absolute;z-index:2;left:0;bottom:0;width:1200px;height:110px}

/* Pricing */
.pricing{top:420px;height:960px;background:var(--teal);color:var(--white)}
.section-kicker{display:block;width:26px;height:3px;background:var(--white);margin-bottom:8px}
.pricing-title{position:absolute;left:300px;top:88px;font-family:"Montserrat",sans-serif;font-weight:800;font-size:26px;letter-spacing:1px}
.pricing-title .section-kicker{position:absolute;left:-42px;top:14px}
.divider{position:absolute;left:600px;top:160px;width:1px;height:760px;background:rgba(255,255,255,.55)}
.plan{position:absolute;width:280px}
.plan-badge{width:92px;height:92px;border-radius:50%;background:var(--white);color:var(--ink);display:flex;align-items:center;justify-content:center;text-align:center;font-family:"Montserrat",sans-serif;font-weight:700;font-size:13px;line-height:16px;margin-bottom:22px}
.plan ul{list-style:none;font-size:11.5px;line-height:20px}
.plan li{display:flex;align-items:center;gap:10px}
.plan li svg{flex:none}
.plan-ds{left:350px;top:160px}
.plan-db{left:686px;top:160px}
.plan-cs{left:350px;top:470px}
.plan-cb{left:686px;top:470px}
.pricing-astronaut{position:absolute;left:40px;top:600px;width:150px;height:210px;border-radius:40% 40% 10% 10%;background:radial-gradient(circle at 50% 40%,#f4f6fa 0,#bfe9dd 50%,rgba(94,201,173,0) 75%)}

/* FAQ */
.faq{top:1380px;height:460px;background:var(--white)}
.faq-title{position:absolute;top:92px;width:1200px;text-align:center;font-family:"Montserrat",sans-serif;font-weight:800;font-size:28px;color:var(--space)}
.faq-title .section-kicker{margin:0 auto 10px;background:var(--space)}
.faq-col{position:absolute;top:150px;width:432px}
.faq-col.left{left:160px}
.faq-col.right{left:618px}
.faq-item{border:1px solid var(--line);margin-bottom:10px;font-size:12px;font-weight:600}
.faq-q{display:flex;justify-content:space-between;align-items:center;padding:10px 14px}
.plus{font-size:16px;font-weight:700;color:var(--ink)}
.faq-item.open{background:var(--teal);border-color:var(--teal);color:var(--white)}
.faq-item.open .plus{color:var(--white)}
.faq-a{padding:2px 14px 16px;font-size:11px;font-weight:400;line-height:17px}

/* CTA */
.cta{top:1840px;height:340px;background:var(--teal-soft);text-align:center}
.cta-title{position:absolute;top:100px;width:1200px;font-family:"Montserrat",sans-serif;font-weight:900;font-size:40px;line-height:46px;color:var(--teal-ink)}
.btn{display:inline-block;background:var(--teal);color:var(--white);font-family:"Montserrat",sans-serif;font-weight:600;font-size:12px;padding:14px 44px;border-radius:24px}
.cta .btn{position:absolute;top:218px;left:518px}

/* Contact */
.contact{top:2180px;height:300px;background:var(--teal);color:var(--white)}
.contact-card{position:absolute;left:188px;top:28px;width:252px;height:236px;background:var(--teal-dark);padding:26px;font-size:11px;line-height:18px}
.contact-card h3{font-family:"Montserrat",sans-serif;font-size:14px;font-weight:700;margin-bottom:40px}
.contact-line{display:flex;gap:10px;align-items:flex-start;margin-bottom:10px}
.contact-line svg{flex:none;margin-top:3px}
.form-title{position:absolute;left:486px;top:40px;font-family:"Montserrat",sans-serif;font-size:24px;font-weight:600}
.form{position:absolute;left:486px;top:96px;width:540px}
.form-row{display:flex;gap:12px;margin-bottom:12px}
.field{flex:1;height:32px;border:1px solid rgba(255,255,255,.75);padding:8px 10px;font-size:11px;color:#effaf6}
.form .btn{background:var(--white);color:var(--teal-ink);border-radius:2px;padding:10px 22px;font-size:11px;margin-top:4px}
.contact-rocket{position:absolute;left:1060px;top:30px;width:110px;height:250px;border-radius:55px 55px 10px 10px;background:linear-gradient(180deg,rgba(255,255,255,.35),rgba(94,201,173,0))}

/* Footer */
.footer{top:2480px;height:124px;background:var(--white);font-size:11px;color:var(--muted)}
.copyright{position:absolute;left:160px;top:46px;line-height:18px}
.foot-menu{position:absolute;left:408px;top:52px;display:flex;gap:32px;list-style:none}
.foot-menu .active{color:var(--teal)}
.social{position:absolute;left:924px;top:46px;display:flex;gap:6px}
.social span{width:22px;height:22px;background:var(--teal-dark);display:block}
.social span:nth-child(2){background:#4aa6d9}
.social span:nth-child(3){background:#3b5998}
.social span:nth-child(4){background:#d9534f}
</style>
</head>
<body>

<header class="hero">
  <nav class="nav">
    <div class="brand"><span class="brand-dot"></span>ORBITRA</div>
    <ul class="menu">
      <li class="active">Home</li><li>About Us</li><li>Service</li><li>Pricing</li><li>Contact Us</li><li>Account</li>
    </ul>
  </nav>
  <div class="hero-rocket" role="img" aria-label="Small rocket illustration flying upward"></div>
  <h1 class="hero-title">Orbitra Is An<br>Omnichannel</h1>
  <p class="hero-sub">Provider For Customer Care</p>
  <div class="hero-astronaut" role="img" aria-label="Illustration of an astronaut floating in space"></div>
  <svg class="hero-clouds" viewBox="0 0 1200 110" preserveAspectRatio="none">
    <path d="M0 70 Q60 30 120 60 Q170 20 240 55 Q300 25 360 60 Q430 30 490 62 Q560 28 620 60 Q690 25 750 58 Q820 30 880 62 Q950 25 1010 58 Q1080 30 1140 60 Q1170 45 1200 55 L1200 110 L0 110 Z" fill="#bfeadf"/>
    <path d="M0 90 Q80 60 150 85 Q230 55 300 85 Q380 58 450 86 Q530 56 600 85 Q680 58 750 86 Q830 56 900 85 Q980 58 1050 86 Q1130 60 1200 82 L1200 110 L0 110 Z" fill="#5ec9ad"/>
  </svg>
</header>

<section class="pricing">
  <h2 class="pricing-title"><span class="section-kicker"></span>PRICING</h2>
  <div class="divider"></div>

  <div class="plan plan-ds">
    <div class="plan-badge">Digital<br>Standard</div>
    <ul>
      <li><svg width="10" height="10" viewBox="0 0 10 10"><path d="M1 5l3 3 5-6" stroke="#fff" stroke-width="1.6" fill="none"/></svg>$99 Per Month</li>
      <li><svg width="10" height="10" viewBox="0 0 10 10"><path d="M1 5l3 3 5-6" stroke="#fff" stroke-width="1.6" fill="none"/></svg>Unlimited Email Support</li>
      <li><svg width="10" height="10" viewBox="0 0 10 10"><path d="M1 5l3 3 5-6" stroke="#fff" stroke-width="1.6" fill="none"/></svg>Unlimited Live Chat Support</li>
      <li><svg width="10" height="10" viewBox="0 0 10 10"><path d="M1 5l3 3 5-6" stroke="#fff" stroke-width="1.6" fill="none"/></svg>Product Research (10 per month)</li>
      <li><svg width="10" height="10" viewBox="0 0 10 10"><path d="M1 5l3 3 5-6" stroke="#fff" stroke-width="1.6" fill="none"/></svg>Product Listing (5 per month)</li>
      <li><svg width="10" height="10" viewBox="0 0 10 10"><path d="M1 5l3 3 5-6" stroke="#fff" stroke-width="1.6" fill="none"/></svg>Price Monitoring (50 products per month)</li>
      <li><svg width="10" height="10" viewBox="0 0 10 10"><path d="M1 5l3 3 5-6" stroke="#fff" stroke-width="1.6" fill="none"/></svg>Product Photo &amp; Video Editing (5 per month)</li>
    </ul>
  </div>

  <div class="plan plan-db">
    <div class="plan-badge">Digital<br>Business</div>
    <ul>
      <li><svg width="10" height="10" viewBox="0 0 10 10"><path d="M1 5l3 3 5-6" stroke="#fff" stroke-width="1.6" fill="none"/></svg>$199 Per Month</li>
      <li><svg width="10" height="10" viewBox="0 0 10 10"><path d="M1 5l3 3 5-6" stroke="#fff" stroke-width="1.6" fill="none"/></svg>Unlimited Email Support</li>
      <li><svg width="10" height="10" viewBox="0 0 10 10"><path d="M1 5l3 3 5-6" stroke="#fff" stroke-width="1.6" fill="none"/></svg>Unlimited Live Chat Support</li>
      <li><svg width="10" height="10" viewBox="0 0 10 10"><path d="M1 5l3 3 5-6" stroke="#fff" stroke-width="1.6" fill="none"/></svg>Product Research (25 per month)</li>
      <li><svg width="10" height="10" viewBox="0 0 10 10"><path d="M1 5l3 3 5-6" stroke="#fff" stroke-width="1.6" fill="none"/></svg>Product Listing (15 per month)</li>
      <li><svg width="10" height="10" viewBox="0 0 10 10"><path d="M1 5l3 3 5-6" stroke="#fff" stroke-width="1.6" fill="none"/></svg>Social Media Posting (20 per month)</li>
      <li><svg width="10" height="10" viewBox="0 0 10 10"><path d="M1 5l3 3 5-6" stroke="#fff" stroke-width="1.6" fill="none"/></svg>Price Monitoring (150 products per month)</li>
      <li><svg width="10" height="10" viewBox="0 0 10 10"><path d="M1 5l3 3 5-6" stroke="#fff" stroke-width="1.6" fill="none"/></svg>Product Photo &amp; Video Editing (15 per month)</li>
    </ul>
  </div>

  <div class="plan plan-cs">
    <div class="plan-badge">Call Center<br>Standard</div>
    <ul>
      <li><svg width="10" height="10" viewBox="0 0 10 10"><path d="M1 5l3 3 5-6" stroke="#fff" stroke-width="1.6" fill="none"/></svg>$0.90 Per Minute / 7 Day Overflow</li>
      <li><svg width="10" height="10" viewBox="0 0 10 10"><path d="M1 5l3 3 5-6" stroke="#fff" stroke-width="1.6" fill="none"/></svg>$49 Per Month</li>
      <li><svg width="10" height="10" viewBox="0 0 10 10"><path d="M1 5l3 3 5-6" stroke="#fff" stroke-width="1.6" fill="none"/></svg>Toll-Free Number</li>
      <li><svg width="10" height="10" viewBox="0 0 10 10"><path d="M1 5l3 3 5-6" stroke="#fff" stroke-width="1.6" fill="none"/></svg>Live Personalized Receptionist</li>
      <li><svg width="10" height="10" viewBox="0 0 10 10"><path d="M1 5l3 3 5-6" stroke="#fff" stroke-width="1.6" fill="none"/></svg>Your Custom Greeting</li>
      <li><svg width="10" height="10" viewBox="0 0 10 10"><path d="M1 5l3 3 5-6" stroke="#fff" stroke-width="1.6" fill="none"/></svg>Includes Inbound &amp; 800 Numbers</li>
      <li><svg width="10" height="10" viewBox="0 0 10 10"><path d="M1 5l3 3 5-6" stroke="#fff" stroke-width="1.6" fill="none"/></svg>Voicemail Transcripts</li>
      <li><svg width="10" height="10" viewBox="0 0 10 10"><path d="M1 5l3 3 5-6" stroke="#fff" stroke-width="1.6" fill="none"/></svg>Appointment Setting</li>
      <li><svg width="10" height="10" viewBox="0 0 10 10"><path d="M1 5l3 3 5-6" stroke="#fff" stroke-width="1.6" fill="none"/></svg>Follow-Up Contacts</li>
      <li><svg width="10" height="10" viewBox="0 0 10 10"><path d="M1 5l3 3 5-6" stroke="#fff" stroke-width="1.6" fill="none"/></svg>Local Call Forwarding</li>
      <li><svg width="10" height="10" viewBox="0 0 10 10"><path d="M1 5l3 3 5-6" stroke="#fff" stroke-width="1.6" fill="none"/></svg>Over-The-Phone Order Taking</li>
      <li><svg width="10" height="10" viewBox="0 0 10 10"><path d="M1 5l3 3 5-6" stroke="#fff" stroke-width="1.6" fill="none"/></svg>Order Status Processing</li>
      <li><svg width="10" height="10" viewBox="0 0 10 10"><path d="M1 5l3 3 5-6" stroke="#fff" stroke-width="1.6" fill="none"/></svg>Weekly Call Reports</li>
      <li><svg width="10" height="10" viewBox="0 0 10 10"><path d="M1 5l3 3 5-6" stroke="#fff" stroke-width="1.6" fill="none"/></svg>Message Delivering Service</li>
      <li><svg width="10" height="10" viewBox="0 0 10 10"><path d="M1 5l3 3 5-6" stroke="#fff" stroke-width="1.6" fill="none"/></svg>Web Integration Of Branding</li>
      <li><svg width="10" height="10" viewBox="0 0 10 10"><path d="M1 5l3 3 5-6" stroke="#fff" stroke-width="1.6" fill="none"/></svg>Complete Call Center Pricing</li>
      <li><svg width="10" height="10" viewBox="0 0 10 10"><path d="M1 5l3 3 5-6" stroke="#fff" stroke-width="1.6" fill="none"/></svg>Customizable For Any Industry</li>
      <li><svg width="10" height="10" viewBox="0 0 10 10"><path d="M1 5l3 3 5-6" stroke="#fff" stroke-width="1.6" fill="none"/></svg>100% US Based Agents</li>
    </ul>
  </div>

  <div class="plan plan-cb">
    <div class="plan-badge">Call Center<br>Business</div>
    <ul>
      <li><svg width="10" height="10" viewBox="0 0 10 10"><path d="M1 5l3 3 5-6" stroke="#fff" stroke-width="1.6" fill="none"/></svg>$0.85 Per Minute / 7 Day Overflow</li>
      <li><svg width="10" height="10" viewBox="0 0 10 10"><path d="M1 5l3 3 5-6" stroke="#fff" stroke-width="1.6" fill="none"/></svg>$99 Per Month</li>
      <li><svg width="10" height="10" viewBox="0 0 10 10"><path d="M1 5l3 3 5-6" stroke="#fff" stroke-width="1.6" fill="none"/></svg>Local Toll-Free Number</li>
      <li><svg width="10" height="10" viewBox="0 0 10 10"><path d="M1 5l3 3 5-6" stroke="#fff" stroke-width="1.6" fill="none"/></svg>Live Personalized Receptionist</li>
      <li><svg width="10" height="10" viewBox="0 0 10 10"><path d="M1 5l3 3 5-6" stroke="#fff" stroke-width="1.6" fill="none"/></svg>Your Custom Greeting</li>
      <li><svg width="10" height="10" viewBox="0 0 10 10"><path d="M1 5l3 3 5-6" stroke="#fff" stroke-width="1.6" fill="none"/></svg>Includes Inbound &amp; 800 Numbers</li>
      <li><svg width="10" height="10" viewBox="0 0 10 10"><path d="M1 5l3 3 5-6" stroke="#fff" stroke-width="1.6" fill="none"/></svg>Outbound Calling</li>
      <li><svg width="10" height="10" viewBox="0 0 10 10"><path d="M1 5l3 3 5-6" stroke="#fff" stroke-width="1.6" fill="none"/></svg>Voicemail Transcripts</li>
      <li><svg width="10" height="10" viewBox="0 0 10 10"><path d="M1 5l3 3 5-6" stroke="#fff" stroke-width="1.6" fill="none"/></svg>Follow-Up Contacts</li>
      <li><svg width="10" height="10" viewBox="0 0 10 10"><path d="M1 5l3 3 5-6" stroke="#fff" stroke-width="1.6" fill="none"/></svg>Customer Upselling</li>
      <li><svg width="10" height="10" viewBox="0 0 10 10"><path d="M1 5l3 3 5-6" stroke="#fff" stroke-width="1.6" fill="none"/></svg>Over-The-Phone Order Taking</li>
      <li><svg width="10" height="10" viewBox="0 0 10 10"><path d="M1 5l3 3 5-6" stroke="#fff" stroke-width="1.6" fill="none"/></svg>Order Status Processing</li>
      <li><svg width="10" height="10" viewBox="0 0 10 10"><path d="M1 5l3 3 5-6" stroke="#fff" stroke-width="1.6" fill="none"/></svg>Detailed Call Reports</li>
      <li><svg width="10" height="10" viewBox="0 0 10 10"><path d="M1 5l3 3 5-6" stroke="#fff" stroke-width="1.6" fill="none"/></svg>Message Delivering Service</li>
      <li><svg width="10" height="10" viewBox="0 0 10 10"><path d="M1 5l3 3 5-6" stroke="#fff" stroke-width="1.6" fill="none"/></svg>Web Integration Of Branding</li>
      <li><svg width="10" height="10" viewBox="0 0 10 10"><path d="M1 5l3 3 5-6" stroke="#fff" stroke-width="1.6" fill="none"/></svg>Complete Call Center Pricing</li>
      <li><svg width="10" height="10" viewBox="0 0 10 10"><path d="M1 5l3 3 5-6" stroke="#fff" stroke-width="1.6" fill="none"/></svg>Customizable For Any Industry</li>
      <li><svg width="10" height="10" viewBox="0 0 10 10"><path d="M1 5l3 3 5-6" stroke="#fff" stroke-width="1.6" fill="none"/></svg>100% US Based Agents</li>
    </ul>
  </div>

  <div class="pricing-astronaut" role="img" aria-label="Illustration of an astronaut standing with a flag"></div>
</section>

<section class="faq">
  <h2 class="faq-title"><span class="section-kicker"></span>Frequently Asked Questions</h2>
  <div class="faq-col left">
    <div class="faq-item open">
      <div class="faq-q">Is There Any Setup Fee? <span class="plus">–</span></div>
      <p class="faq-a">There is no setup fee and no hidden charges. Once you choose a plan, our team builds your script, sets up your number and trains your agents at no extra cost, so you can start taking calls within days.</p>
    </div>
    <div class="faq-item"><div class="faq-q">Do you offer custom script writing? <span class="plus">+</span></div></div>
    <div class="faq-item"><div class="faq-q">Why do you use time-based billing over standard billing? <span class="plus">+</span></div></div>
    <div class="faq-item"><div class="faq-q">How long does it take to get started? <span class="plus">+</span></div></div>
  </div>
  <div class="faq-col right">
    <div class="faq-item"><div class="faq-q">Do I have to sign a contract? <span class="plus">+</span></div></div>
    <div class="faq-item"><div class="faq-q">Do I have to purchase any hardware or equipment? <span class="plus">+</span></div></div>
    <div class="faq-item"><div class="faq-q">I'm not sure how many minutes I'll need? <span class="plus">+</span></div></div>
    <div class="faq-item"><div class="faq-q">Can I change my service plan? <span class="plus">+</span></div></div>
  </div>
</section>

<section class="cta">
  <h2 class="cta-title">READY TO TAKE YOUR BUSINESS<br>TO THE NEXT LEVEL</h2>
  <span class="btn">Get Started</span>
</section>

<section class="contact">
  <div class="contact-card">
    <h3>Contact Details</h3>
    <div class="contact-line"><svg width="12" height="12" viewBox="0 0 12 12"><path d="M2 1h3l1 3-2 1a7 7 0 0 0 3 3l1-2 3 1v3a1 1 0 0 1-1 1A10 10 0 0 1 1 2a1 1 0 0 1 1-1z" fill="#fff"/></svg><span>Phone: (555) 014-2290</span></div>
    <div class="contact-line"><svg width="12" height="12" viewBox="0 0 12 12"><rect x="1" y="2.5" width="10" height="7" fill="none" stroke="#fff"/><path d="M1 3l5 4 5-4" fill="none" stroke="#fff"/></svg><span>hello@orbitracare.example</span></div>
    <div class="contact-line"><svg width="12" height="12" viewBox="0 0 12 12"><path d="M6 11s4-4 4-6.5A4 4 0 0 0 2 4.5C2 7 6 11 6 11z" fill="#fff"/><circle cx="6" cy="4.5" r="1.4" fill="#3fae93"/></svg><span>418 Orbit Lane, Suite 12<br>Lakemont, CA 90210</span></div>
  </div>
  <h2 class="form-title">Request For Call Back</h2>
  <div class="form">
    <div class="form-row"><div class="field">Name</div><div class="field">Email</div><div class="field">Phone Number</div></div>
    <div class="form-row"><div class="field">Company Name</div><div class="field">Message</div></div>
    <span class="btn">Submit Now</span>
  </div>
  <div class="contact-rocket" role="img" aria-label="Faint rocket illustration launching"></div>
</section>

<footer class="footer">
  <p class="copyright">Copyright © 2024<br>All Rights Reserved</p>
  <ul class="foot-menu"><li class="active">Home</li><li>About Us</li><li>Service</li><li>Pricing</li><li>Contact Us</li><li>Account</li></ul>
  <div class="social"><span></span><span></span><span></span><span></span></div>
</footer>

</body>
</html>
```